Business Card Design For Marketing Agnecy LVP

Need business card design for marketing agency.

Doug Fenwick
President, CEO
1-555-302-4196
doug@boldpromoperksgroup.example
www.BoldPromoPerksGroup.example

Back Side:
Boost Sales Using Rewards, Incentives & Giveaways
Get A Free Sample Package

Target Market(s)

B2B

Industry/Entity Type

Marketing

Contact Information for Business Card

Doug Fenwick
President, CEO
1-555-302-4196

Back Side:
Get A Free Sample Package

Please note that my current url is OLD DESIGN. I am working on new design and want the business card to match color themes at least on new site. Here is the demo link for new site so you can see the colors I use, etc.

http://layoutcratehub.example/kq/doug/lvp_final/index.html

Requirements
Must have
• Please note that my current url is OLD DESIGN. I am working on new design and want the business card to match color themes at least on new site. Here is the demo link for new site so you can see the colors I use, etc.

Nice to have

Should not have

```html
<!DOCTYPE html>
<html lang="en">
<head>
<meta charset="utf-8">
<title>LVP Business Card</title>
<link href="https://fonts.googleapis.com/css2?family=Montserrat:wght@400;500;700&family=Roboto:wght@400;500;700&display=swap" rel="stylesheet">
<style>
  :root {
    --brand-blue: #1177c0;
    --ink-grey: #4a4a4c;
    --rule-grey: #5a5a5c;
    --card-white: #ffffff;
    --backdrop: #e9eaec;
  }
  * { margin: 0; padding: 0; box-sizing: border-box; }
  html, body { width: 1200px; height: 900px; overflow: hidden; }
  body { background: var(--backdrop); position: relative; font-family: "Montserrat", sans-serif; }

  .card {
    position: absolute;
    width: 560px;
    height: 320px;
    border-radius: 4px;
    box-shadow: 0 6px 18px rgba(0,0,0,0.12);
    overflow: hidden;
  }

  /* Back side */
  .card-back { left: 70px; top: 80px; background: var(--brand-blue); color: var(--card-white); }
  .back-mark {
    position: absolute; left: 0; right: 0; top: 78px;
    display: flex; justify-content: center; align-items: center; gap: 14px;
  }
  .back-mark .mark-dot { width: 20px; height: 20px; border-radius: 50%; background: var(--card-white); }
  .back-mark .mark-name { font-family: "Montserrat", sans-serif; font-weight: 700; font-size: 84px; letter-spacing: 2px; line-height: 1; }
  .back-url { position: absolute; left: 0; right: 0; top: 222px; text-align: center; font-size: 15px; font-weight: 400; letter-spacing: 0.3px; }
  .back-tagline { position: absolute; left: 0; right: 0; top: 262px; text-align: center; font-size: 13.5px; font-weight: 400; letter-spacing: 0.2px; }

  /* Front side */
  .card-front { left: 570px; top: 500px; background: var(--card-white); font-family: "Roboto", sans-serif; }
  .front-mark {
    position: absolute; right: 40px; top: 36px;
    display: flex; align-items: center; gap: 10px;
  }
  .front-mark .mark-dot { width: 14px; height: 14px; border-radius: 50%; background: var(--brand-blue); }
  .front-mark .mark-name { font-family: "Montserrat", sans-serif; font-weight: 700; font-size: 52px; color: var(--brand-blue); line-height: 1; letter-spacing: 1px; }
  .front-rule { position: absolute; left: 215px; right: 34px; top: 180px; height: 1.5px; background: var(--rule-grey); }
  .edge-tab { position: absolute; left: -14px; top: 232px; width: 28px; height: 38px; border-radius: 0 14px 14px 0; background: var(--brand-blue); }

  .holder { position: absolute; left: 36px; top: 160px; }
  .holder-name { font-family: "Roboto", sans-serif; font-weight: 700; font-size: 24px; color: var(--brand-blue); letter-spacing: 0.3px; text-transform: uppercase; }
  .holder-title { font-size: 16px; color: var(--ink-grey); margin-top: 2px; }

  .contact-list { position: absolute; left: 46px; top: 234px; list-style: none; }
  .contact-list li { display: flex; align-items: center; gap: 9px; font-size: 15px; color: var(--ink-grey); line-height: 22px; }
  .contact-list svg { width: 12px; height: 12px; fill: var(--brand-blue); flex: none; }
</style>
</head>
<body>

<section class="card card-back" aria-label="Card back">
  <div class="back-mark">
    <span class="mark-dot"></span>
    <span class="mark-name">LVP</span>
  </div>
  <p class="back-url">www.BoldPromoPerksGroup.example</p>
  <p class="back-tagline">Boost Sales Using Rewards I Incentives &amp; Giveaways I Get A Free Sample Package</p>
</section>

<section class="card card-front" aria-label="Card front">
  <div class="front-mark">
    <span class="mark-dot"></span>
    <span class="mark-name">LVP</span>
  </div>
  <div class="front-rule"></div>
  <div class="edge-tab"></div>

  <div class="holder">
    <h1 class="holder-name">Doug Fenwick</h1>
    <p class="holder-title">President, CEO</p>
  </div>

  <ul class="contact-list">
    <li>
      <svg viewBox="0 0 12 12" aria-hidden="true"><path d="M3 1 L5 3.5 L4 5 Q5 7 7 8 L8.5 7 L11 9 L9.5 11 Q5 11 1 3 Z"/></svg>
      1-555-302-4196
    </li>
    <li>
      <svg viewBox="0 0 12 12" aria-hidden="true"><path d="M1 2.5 H11 V9.5 H1 Z M1.6 3 L6 6.6 L10.4 3 Z" fill-rule="evenodd"/></svg>
      doug@boldpromoperksgroup.example
    </li>
    <li>
      <svg viewBox="0 0 12 12" aria-hidden="true"><circle cx="6" cy="6" r="5.2"/><path d="M1 6 H11 M6 1 V11" stroke="#fff" stroke-width="0.8"/></svg>
      www.BoldPromoPerksGroup.example
    </li>
  </ul>
</section>

</body>
</html>
```